New Business Card Design Project LORVANTI-Italy

we are LORVANTI-Italy
our company in the market for 3 years we are luxury cosmetic company and its about time for a facelift :)
i will like to have elegant luxurious and unique business card
that will give the person that get it a unique, luxurious and elegant impression
I'm VERY OPEN FOR NEW IDEAS , even duo i add a few files of things that i see on line and i like them

i add my logo as well
my website is LORVANTI.COM
(if you would like to see the main style that we have)

Target Market(s)

adult that have money :)

Industry/Entity Type

Business

Contact Information for Business Card

Name - Dario Lorvanti
Position - CEO and CO Founder
address - 4817 E Halvern
telephone - 555-384-1926
email - dario@lorvanti.com
fax - 555-384-1926
website - LORVANTI.COM

Colors
000000
959595
fbee3e
ffffff

Requirements
Must have
• big logo in GOLD color
• elegant look
• impressive
Nice to have
• not must but maybe classy pattern background
• not must but maybe emblem
• maybe clear plastic business card
Should not have
• colors
• images

```html
<!DOCTYPE html>
<html lang="en">
<head>
<meta charset="utf-8">
<title>LORVANTI Italy – Business Card</title>
<link href="https://fonts.googleapis.com/css2?family=Cinzel:wght@400&family=Roboto:wght@400&display=swap" rel="stylesheet">
<style>
  :root {
    --canvas-bg: #d9d6d2;
    --card-black: #000000;
    --card-dark: #161616;
    --card-mid: #222222;
    --gold: #d9b63a;
    --grey: #959595;
    --white: #ffffff;
  }
  html, body {
    margin: 0;
    padding: 0;
    width: 1200px;
    height: 1200px;
    overflow: hidden;
    background: var(--canvas-bg);
  }
  .canvas {
    position: relative;
    width: 1200px;
    height: 1200px;
  }
  .card {
    position: absolute;
    left: 214px;
    width: 773px;
    height: 440px;
    background: linear-gradient(135deg, var(--card-mid) 0%, var(--card-dark) 45%, var(--card-black) 100%);
    box-shadow: 0 6px 18px rgba(0,0,0,0.35);
    overflow: hidden;
  }
  .card--front { top: 149px; }
  .card--back { top: 633px; }

  .brand {
    position: absolute;
    text-align: center;
    color: var(--gold);
    font-family: "Cinzel", serif;
    font-weight: 400;
  }
  .brand__mark {
    display: block;
    margin: 0 auto;
    border: 3px solid var(--gold);
    border-radius: 50%;
    box-sizing: border-box;
  }
  .brand__name {
    display: block;
    line-height: 1;
    letter-spacing: 1px;
  }
  .brand__rule {
    display: block;
    height: 2px;
    background: var(--gold);
    margin: 0 auto;
  }
  .brand__place {
    display: block;
    line-height: 1;
    letter-spacing: 1px;
  }

  /* front */
  .card--front .brand { left: 46px; top: 84px; width: 322px; }
  .card--front .brand__mark { width: 126px; height: 126px; }
  .card--front .brand__name { font-size: 48px; margin-top: 36px; }
  .card--front .brand__rule { width: 280px; margin-top: 10px; }
  .card--front .brand__place { font-size: 20px; margin-top: 10px; }

  .divider {
    position: absolute;
    left: 388px;
    top: 99px;
    width: 2px;
    height: 244px;
    background: var(--gold);
  }
  .person {
    position: absolute;
    left: 430px;
    top: 84px;
  }
  .person__name {
    margin: 0;
    font-family: "Cinzel", serif;
    font-weight: 400;
    font-size: 32px;
    letter-spacing: 2px;
    color: var(--gold);
  }
  .person__role {
    margin: 2px 0 0;
    font-family: "Roboto", sans-serif;
    font-size: 18px;
    color: var(--grey);
  }
  .contact {
    list-style: none;
    margin: 44px 0 0;
    padding: 0;
    font-family: "Roboto", sans-serif;
    font-size: 17px;
    line-height: 31px;
    color: var(--white);
  }

  /* back */
  .lattice {
    position: absolute;
    inset: 0;
    background: radial-gradient(ellipse at 70% 20%, #2a2a2a 0%, #141414 55%, #050505 100%);
  }
  .card--back .brand { left: 0; top: 80px; width: 773px; }
  .card--back .brand__mark { width: 138px; height: 138px; }
  .card--back .brand__name { font-size: 60px; margin-top: 34px; }
  .card--back .brand__rule { width: 330px; margin-top: 12px; }
  .card--back .brand__place { font-size: 22px; margin-top: 12px; }
</style>
</head>
<body>
<main class="canvas">
  <section class="card card--front" aria-label="Business card front">
    <div class="brand">
      <span class="brand__mark" aria-hidden="true"></span>
      <span class="brand__name">LORVANTI</span>
      <span class="brand__rule" aria-hidden="true"></span>
      <span class="brand__place">ITALY</span>
    </div>
    <span class="divider" aria-hidden="true"></span>
    <div class="person">
      <h1 class="person__name">DARIO LORVANTI</h1>
      <p class="person__role">CEO and CO Founder</p>
      <ul class="contact">
        <li>Tel. 555-384-1926</li>
        <li>Fax. 555-384-1926</li>
        <li>dario@lorvanti.com</li>
        <li>www.lorvanti.com</li>
        <li>Address. 4817 E Halvern</li>
      </ul>
    </div>
  </section>

  <section class="card card--back" aria-label="Business card back">
    <div class="lattice" role="img" aria-label="Fine diagonal lattice pattern on black"></div>
    <div class="brand">
      <span class="brand__mark" aria-hidden="true"></span>
      <span class="brand__name">LORVANTI</span>
      <span class="brand__rule" aria-hidden="true"></span>
      <span class="brand__place">ITALY</span>
    </div>
  </section>
</main>
</body>
</html>
```